Harbourline Physiotherapy business card design

We need a fresh, new business card design for our physiotherapy clinic Harbourline Physiotherapy

Will attach logo soon we had logo designed from our last project

Industry/Entity Type

Physical Therapy

Contact Information for Business Card

On front
Needs our logo, contact details:
58 Wexley Lane St Clair NSW 2759
Ph/f: 02 9481 2057
info@harbourlinephysio.example.com.au

Requirements
Must have
• On the back of the card needs to have area to write down follow up appointments
• On front
• Needs our logo
• The colours have to be the colours in our logo which are: sky blue, black and white
• Font to be same as our logo please
• We want the card to look simple, not too cluttered but to the point
Should not have
• We don't need any extra pictures other than our logo

```html
<!DOCTYPE html>
<html lang="en">
<head>
<meta charset="utf-8">
<title>Harbourline Physiotherapy – Business Card</title>
<link rel="stylesheet" href="https://fonts.googleapis.com/css2?family=Open+Sans:wght@400;600;700&display=swap">
<style>
  :root {
    --bg: #ecebe8;
    --card: #ffffff;
    --sky: #2f86d6;
    --royal: #2645b0;
    --navy: #1c2d78;
    --ink: #3a3a3a;
    --grey: #5d5f66;
    --dots: #7fa6d8;
    --shadow: rgba(0,0,0,0.18);
  }
  * { margin: 0; padding: 0; box-sizing: border-box; }
  html, body { width: 1200px; height: 843px; overflow: hidden; background: var(--bg); }
  body { position: relative; font-family: "Open Sans", sans-serif; color: var(--ink); }

  .card {
    position: absolute;
    width: 640px; height: 366px;
    background: linear-gradient(160deg, #ffffff 0%, #f4f5f7 100%);
    box-shadow: 0 10px 28px var(--shadow);
    overflow: hidden;
  }
  .card-back { left: 60px; top: 50px; }
  .card-front { left: 500px; top: 427px; }

  /* Back: appointment card */
  .mark-area {
    position: absolute; left: 60px; top: 40px;
    width: 170px; height: 290px; border-radius: 50%;
    background: radial-gradient(ellipse at center, rgba(140,170,210,0.22) 0%, rgba(140,170,210,0) 70%);
  }
  .appt-title {
    position: absolute; right: 40px; top: 28px;
    font-size: 21px; font-weight: 700; color: var(--royal);
  }
  .appt-row {
    position: absolute; left: 40px; right: 40px;
    display: flex; align-items: flex-end; gap: 8px;
    font-size: 16px; color: var(--royal);
  }
  .appt-row .fill { flex: 1; border-bottom: 2px dotted var(--dots); height: 1px; margin-bottom: 4px; }
  .row-name { top: 78px; }
  .row-date { top: 126px; }
  .row-days { top: 174px; gap: 14px; }
  .row-note { top: 222px; }
  .row-extra { top: 250px; left: 110px; }
  .ampm { font-size: 11px; align-self: flex-start; margin-top: -10px; }
  .day { display: flex; align-items: center; gap: 6px; }
  .tick-box { width: 14px; height: 14px; border: 1.5px solid var(--grey); background: #fff; }
  .appt-note {
    position: absolute; left: 110px; right: 40px; top: 300px;
    font-size: 11px; color: var(--grey); text-align: center;
  }

  /* Front */
  .brand { position: absolute; left: 40px; top: 44px; display: flex; align-items: center; gap: 14px; }
  .brand-dot { width: 34px; height: 34px; border-radius: 50%; background: var(--sky); }
  .brand-name { font-size: 30px; font-weight: 700; color: var(--royal); letter-spacing: 0.2px; }
  .rule { position: absolute; left: 90px; top: 128px; width: 520px; height: 2px;
    background: linear-gradient(90deg, rgba(38,69,176,0) 0%, var(--royal) 60%, var(--navy) 100%); }
  .person { position: absolute; right: 40px; top: 140px; text-align: right; }
  .person-name { font-size: 22px; font-weight: 700; color: var(--navy); }
  .person-role { font-size: 16px; color: var(--ink); border-bottom: 2px solid var(--navy); padding-bottom: 2px; }
  .contacts { position: absolute; left: 36px; top: 138px; list-style: none; font-size: 14px; color: var(--ink); }
  .contacts li { display: flex; align-items: center; gap: 10px; height: 22px; }
  .contacts svg { width: 14px; height: 14px; fill: var(--navy); }
  .address { position: absolute; right: 40px; top: 236px; text-align: right; font-size: 15px; line-height: 1.4; color: var(--ink); font-style: normal; }
  .swoosh { position: absolute; left: 0; bottom: 0; width: 640px; height: 366px; }
</style>
</head>
<body>

<section class="card card-back" aria-label="Appointment card, back">
  <div class="mark-area" role="img" aria-label="Faint brand mark area"></div>
  <h2 class="appt-title">Next Appointment</h2>
  <div class="appt-row row-name"><span>Name :</span><span class="fill"></span><span>Time :</span><span class="fill"></span><span class="ampm">AM/PM</span></div>
  <div class="appt-row row-date"><span>Date :</span><span class="fill"></span></div>
  <div class="appt-row row-days">
    <span class="day">Sun <i class="tick-box"></i></span>
    <span class="day">Mon <i class="tick-box"></i></span>
    <span class="day">Tue <i class="tick-box"></i></span>
    <span class="day">Wed <i class="tick-box"></i></span>
    <span class="day">Thu <i class="tick-box"></i></span>
    <span class="day">Fri <i class="tick-box"></i></span>
    <span class="day">Sat <i class="tick-box"></i></span>
  </div>
  <div class="appt-row row-note"><span>Note :</span><span class="fill"></span></div>
  <div class="appt-row row-extra"><span class="fill"></span></div>
  <p class="appt-note">Please give us 24 hours notice if you need to change or cancel your appointment.</p>
</section>

<section class="card card-front" aria-label="Business card, front">
  <svg class="swoosh" viewBox="0 0 640 366" aria-hidden="true">
    <defs>
      <linearGradient id="blueBand" x1="0" y1="0" x2="1" y2="0">
        <stop offset="0" stop-color="#2a3fb0"/>
        <stop offset="0.5" stop-color="#2f86d6"/>
        <stop offset="1" stop-color="#2645b0"/>
      </linearGradient>
      <linearGradient id="greyBand" x1="0" y1="0" x2="1" y2="0">
        <stop offset="0" stop-color="#3b3d44"/>
        <stop offset="1" stop-color="#9a9ca3"/>
      </linearGradient>
    </defs>
    <path d="M0,232 Q260,318 640,356 L640,362 Q250,330 0,258 Z" fill="url(#greyBand)"/>
    <path d="M0,262 Q250,334 640,364 L640,366 L0,366 Z" fill="url(#blueBand)"/>
    <path d="M0,268 Q250,336 640,365" fill="none" stroke="#9fd0f5" stroke-width="1.5" opacity="0.7"/>
  </svg>

  <div class="brand">
    <span class="brand-dot"></span>
    <span class="brand-name">Harbourline Physiotherapy</span>
  </div>
  <div class="rule"></div>

  <ul class="contacts">
    <li><svg viewBox="0 0 24 24"><path d="M6.6 10.8a15 15 0 0 0 6.6 6.6l2.2-2.2a1 1 0 0 1 1-.25 11 11 0 0 0 3.6.6 1 1 0 0 1 1 1V20a1 1 0 0 1-1 1A17 17 0 0 1 3 4a1 1 0 0 1 1-1h3.5a1 1 0 0 1 1 1 11 11 0 0 0 .6 3.6 1 1 0 0 1-.25 1z"/></svg>02 9481 2057</li>
    <li><svg viewBox="0 0 24 24"><path d="M6 3h10v5H6zM3 9h18v9h-3v3H6v-3H3zM8 15v4h8v-4z"/></svg>02 9481 2057</li>
    <li><svg viewBox="0 0 24 24"><path d="M2 5h20v14H2zM4 7v.5l8 5 8-5V7z"/></svg>info@harbourlinephysio.example.com.au</li>
    <li><svg viewBox="0 0 24 24"><circle cx="12" cy="12" r="10"/></svg>www.harbourlinephysio.example.com.au</li>
  </ul>

  <div class="person">
    <p class="person-name">Daniel Hart</p>
    <p class="person-role">CEO/Founder</p>
  </div>

  <address class="address">58 Wexley Lane Kelvin Ridge<br>NSW 2791</address>
</section>

</body>
</html>
```